Velmori Chatterly Ads Design (examples provided)

We provide Plexor Chart Studio, Plexor Grids and Tandrel Tabula Connectors and templates. https://vistaboard.plexor.example/
Our core audience is Digital marketing agencies, but anyone who owns a business and uses any of these ad platforms https://velmori-frontend.quandrilabs.example/product-data-connector can use our connectors and reports.
I am looking to have high converting Chatterly ad & Plexor Display images made. Our website is here (in progress) the domain is Velmori.ai
Tagline -
Clear Numbers, Zero Fuss
Few Features we have -
Free Forever Plan
Free High-end Templates
Popular chart studio connectors -
https://velmori-frontend.quandrilabs.example/product-data-connector
I would like the designs to have black background and be VIBRANT, visuals that will stop users from scrolling on Chatterly.
Nice designs but please - I have attached 4 concepts that I would like each designer to COPY but use my site's color scheme and swap out the people with new versions, putting your own spin on the designs. These are the highest converting SaaS designs of 2023, so I know they work, I just need versions for my brand.
Updates
Here are specific details https://papers.plexor.example/document/d/7Kq-wm4TRB_hPlaXaRvoJkdWnRtpLsHvb2eFeQz8yM4r/edit?usp=sharing
Target Market(s)
Digital marketing's agencies or anyone with a business' that uses Plexor chart studio
Look and feel

```html
<!DOCTYPE html>
<html lang="en">
<head>
<meta charset="utf-8">
<title>Velmori.ai — Clear Numbers, Zero Fuss</title>
<link href="https://fonts.googleapis.com/css2?family=Poppins:wght@400;500;800;900&display=swap" rel="stylesheet">
<style>
  :root {
    --bg-deep: #06070b;
    --bg-navy: #0d1320;
    --bg-glow: #0f2a3a;
    --circuit-line: rgba(120, 150, 190, 0.10);
    --text-white: #ffffff;
    --accent-blue: #1a8cff;
    --accent-violet: #8f5fe0;
    --accent-pink: #e8509a;
    --photo-base-top: #3a3c44;
    --photo-base-bottom: #17181d;
    --photo-red: #c4262c;
    --photo-grey: #9a9ea6;
    --photo-black: #0c0c0f;
  }
  * { margin: 0; padding: 0; box-sizing: border-box; }
  html, body { width: 1200px; height: 1200px; overflow: hidden; background: var(--bg-deep); }
  .ad-canvas {
    position: relative;
    width: 1200px;
    height: 1200px;
    overflow: hidden;
    font-family: "Poppins", sans-serif;
    color: var(--text-white);
    background:
      radial-gradient(ellipse 80% 30% at 50% 100%, var(--bg-glow) 0%, transparent 75%),
      radial-gradient(ellipse 60% 50% at 20% 30%, var(--bg-navy) 0%, transparent 75%),
      var(--bg-deep);
  }
  .circuit-lines {
    position: absolute;
    inset: 0;
    width: 1200px;
    height: 1200px;
  }
  .floor-glow {
    position: absolute;
    left: 0;
    top: 1000px;
    width: 1200px;
    height: 200px;
    background: linear-gradient(180deg, transparent 0%, rgba(40, 110, 150, 0.22) 70%, rgba(40, 110, 150, 0.30) 100%);
  }
  .headline {
    position: absolute;
    left: 77px;
    top: 104px;
    font-weight: 500;
    font-size: 100px;
    line-height: 118px;
    letter-spacing: -1px;
  }
  .headline .line { display: block; }
  .headline .highlight {
    display: inline-block;
    font-weight: 900;
    font-size: 114px;
    line-height: 128px;
    background: linear-gradient(90deg, var(--accent-blue) 0%, var(--accent-violet) 50%, var(--accent-pink) 100%);
    -webkit-background-clip: text;
    background-clip: text;
    color: transparent;
  }
  .headline-underline {
    position: absolute;
    left: 70px;
    top: 588px;
    width: 500px;
    height: 30px;
  }
  .feature-text {
    position: absolute;
    left: 77px;
    top: 638px;
    font-weight: 400;
    font-size: 41px;
    line-height: 48px;
  }
  .hero-photo {
    position: absolute;
    left: 470px;
    top: 420px;
    width: 680px;
    height: 620px;
    border-radius: 48px 48px 120px 48px;
    background:
      radial-gradient(ellipse 26% 22% at 62% 34%, var(--photo-red) 0%, rgba(196, 38, 44, 0.6) 55%, transparent 100%),
      radial-gradient(ellipse 40% 18% at 40% 66%, var(--photo-grey) 0%, rgba(154, 158, 166, 0.5) 55%, transparent 100%),
      radial-gradient(ellipse 50% 45% at 78% 62%, var(--photo-black) 0%, transparent 90%),
      linear-gradient(160deg, var(--photo-base-top) 0%, var(--photo-base-bottom) 100%);
    border: 1px solid rgba(255, 255, 255, 0.08);
    box-shadow: 0 30px 80px rgba(0, 0, 0, 0.6), 0 0 60px rgba(143, 95, 224, 0.18);
  }
  .offer-badge {
    position: absolute;
    left: 800px;
    top: 118px;
    width: 340px;
    height: 260px;
  }
  .offer-badge text { font-family: "Poppins", sans-serif; fill: var(--text-white); }
  .brand-signoff {
    position: absolute;
    left: 767px;
    top: 1078px;
    display: flex;
    align-items: center;
    gap: 18px;
  }
  .brand-dot {
    width: 66px;
    height: 66px;
    border-radius: 50%;
    background: var(--accent-violet);
  }
  .brand-divider {
    width: 3px;
    height: 76px;
    background: var(--text-white);
  }
  .brand-name {
    font-weight: 400;
    font-size: 53px;
    color: var(--text-white);
  }
</style>
</head>
<body>
<main class="ad-canvas">
  <svg class="circuit-lines" viewBox="0 0 1200 1200" aria-hidden="true">
    <g fill="none" stroke="var(--circuit-line)" stroke-width="2">
      <path d="M0 760 H160 L220 820 V1000"/>
      <path d="M0 880 H120 L180 940"/>
      <path d="M60 640 V700 L120 760"/>
      <path d="M1200 470 H1080 L1040 430 V300"/>
      <path d="M1200 560 H1120 L1090 590 V700"/>
    </g>
    <g fill="var(--circuit-line)">
      <circle cx="220" cy="1000" r="6"/>
      <circle cx="180" cy="940" r="6"/>
      <circle cx="1040" cy="300" r="6"/>
    </g>
  </svg>
  <div class="floor-glow" aria-hidden="true"></div>

  <div class="hero-photo" role="img" aria-label="Photo of a young man in a red t-shirt and grey jeans relaxing in a black bean bag chair, working on a laptop with headphones around his neck"></div>

  <h1 class="headline">
    <span class="line">Clear</span>
    <span class="line">Numbers,</span>
    <span class="line">Zero</span>
    <span class="line highlight">Fuss</span>
  </h1>

  <svg class="headline-underline" viewBox="0 0 500 30" aria-hidden="true">
    <defs>
      <linearGradient id="underlineGradient" x1="0" x2="1" y1="0" y2="0">
        <stop offset="0" stop-color="#1a8cff"/>
        <stop offset="0.55" stop-color="#8f5fe0"/>
        <stop offset="1" stop-color="#e8509a" stop-opacity="0.3"/>
      </linearGradient>
    </defs>
    <path d="M4 22 Q 240 4 496 12 Q 240 10 4 26 Z" fill="url(#underlineGradient)"/>
  </svg>

  <p class="feature-text">Free High-end<br>Templates</p>

  <svg class="offer-badge" viewBox="0 0 340 260" role="img" aria-label="Free Forever Plan">
    <defs>
      <linearGradient id="badgeGradient" x1="0" x2="1" y1="0" y2="0">
        <stop offset="0" stop-color="#1a8cff"/>
        <stop offset="0.5" stop-color="#8f5fe0"/>
        <stop offset="1" stop-color="#e8509a"/>
      </linearGradient>
    </defs>
    <g transform="rotate(-6 170 120)">
      <path d="M24 40 Q24 24 40 24 L300 24 Q316 24 316 40 L316 160 Q316 176 300 176 L222 176 L200 236 L176 176 L40 176 Q24 176 24 160 Z" fill="url(#badgeGradient)"/>
      <text x="170" y="112" text-anchor="middle" font-size="76" font-weight="900">FREE</text>
      <text x="170" y="152" text-anchor="middle" font-size="29" font-weight="800">FOREVER PLAN</text>
    </g>
  </svg>

  <div class="brand-signoff">
    <span class="brand-dot" aria-hidden="true"></span>
    <span class="brand-divider" aria-hidden="true"></span>
    <span class="brand-name">Velmori.ai</span>
  </div>
</main>
</body>
</html>
```